Expedition Cruise Sales Website for the Polar Regions (Antarctica & Arctic)

This will be a website for selling cruises.
This site should have a homepage, a ship page, destinations, and itineraries.
I have created a file specifying each page, and it is attached.
Pages:
1. Home
2. Cruise Lines
- 2.1 Ships
3. Destinations
- 3.1 Region - 3.2 Country - 3.3 City
4. Itineraries
- 4.1 Itinerary
5. Blog / Travel Tips 6. About Us
7. Contact
Please take a look on the attached pdf
Target Market(s)
Expedition Travelers
Coding
Coded - Design and coding required
Number of Pages Required
5+ page
Font styles to use
Look and feel
Each slider illustrates characteristics of the customer's brand and the style your logo design should communicate.

```html
<!DOCTYPE html>
<html lang="en">
<head>
<meta charset="utf-8">
<title>Glacera — Expedition Cruises</title>
<link href="https://fonts.googleapis.com/css2?family=Poppins:wght@400;500;600&family=Lato:ital,wght@0,400;0,700;1,400&display=swap" rel="stylesheet">
<style>
:root{
  --blue:#2b6cb8;
  --blue-dark:#1d4f93;
  --navy:#0f2a55;
  --ink:#1b1b1b;
  --pale:#d3e5f8;
  --card:#dbe9f9;
  --white:#fff;
  --star:#e0a800;
}
*{margin:0;padding:0;box-sizing:border-box}
html,body{width:1200px;height:3490px;overflow:hidden}
body{position:relative;font-family:'Lato',sans-serif;color:var(--ink);background:var(--white)}
.abs{position:absolute}
.head{font-family:'Poppins',sans-serif;font-weight:400}
.accent{color:var(--blue)}

/* hero */
.hero{left:0;top:0;width:1200px;height:562px;overflow:hidden}
.hero-scene{left:0;top:0;width:1200px;height:562px;
  background:linear-gradient(180deg,#8fc3ec 0%,#b9dcf3 32%,#5fc0dc 48%,#1fa6c9 70%,#1d8fb8 100%)}
.hero-wave{left:0;top:440px}
.nav{left:111px;top:34px;width:976px;height:68px;background:var(--white);border-radius:14px;
  display:flex;align-items:center;padding:0 0 0 38px;font-size:15px}
.nav a{color:var(--ink);text-decoration:none;margin-right:21px}
.nav a.on{color:var(--blue)}
.nav .right{margin-left:214px}
.nav .cta{margin-left:auto;margin-right:20px;background:var(--blue);color:#fff;border-radius:10px;
  padding:13px 21px;font-size:17px;font-weight:700}
.logo-disc{left:536px;top:-4px;width:130px;height:130px;border-radius:50%;background:var(--white);
  display:flex;align-items:flex-end;justify-content:center;padding-bottom:36px}
.brand{font-family:'Poppins',sans-serif;font-weight:600;color:var(--blue);font-size:24px}
.hero h1{left:111px;top:200px;font-size:46px;line-height:61px;color:var(--ink);font-family:'Poppins',sans-serif;font-weight:400}
.hero h1 span{color:var(--navy);font-weight:500}
.btn{background:var(--blue);color:#fff;border-radius:12px;font-weight:700;display:flex;align-items:center;justify-content:center}
.get{left:111px;top:338px;width:129px;height:44px;font-size:19px}
.search{left:108px;top:420px;width:980px;height:85px;background:var(--white);border-radius:14px;
  display:flex;align-items:center;padding:0 20px;gap:22px}
.chip{height:40px;border:1px solid #e3e6ea;box-shadow:0 2px 4px rgba(0,0,0,.08);border-radius:4px;
  display:flex;align-items:center;gap:12px;padding:0 12px;font-size:16px;font-weight:700}
.chip svg{width:20px;height:20px}
.sbtn{margin-left:auto;width:140px;height:52px;font-size:18px;gap:12px}

/* offers */
.sec-title{width:1200px;text-align:center;font-size:39px}
.offer{width:330px;text-align:center}
.offer .pic{width:304px;height:304px;border-radius:50%;margin:0 auto}
.offer h3{margin-top:22px;font-size:22px;font-weight:700}
.offer p{font-size:13.5px;line-height:26px;margin-top:10px}
.offer.sel h3,.offer.sel p{color:var(--blue)}

/* destinations */
.dest{left:0;top:1300px;width:1200px;height:605px;background:var(--pale)}
.dest h2{top:80px;color:var(--blue);font-weight:500}
.dcard{top:179px;width:232px;text-align:center}
.dcard .pic{height:260px;border-radius:12px}
.dcard.sel .pic{outline:3px solid var(--blue)}
.dcard span{display:block;margin-top:30px;font-size:22px;font-weight:500}
.dcard.sel span{color:var(--blue)}
.arrow{top:305px}

/* testimonials */
.tcard{top:2085px;width:446px;height:184px;background:var(--card);border-radius:10px;
  box-shadow:0 4px 10px rgba(0,0,0,.06);text-align:center;padding:20px 46px 0}
.quote{position:absolute;left:118px;top:-18px;font-family:Georgia,serif;font-size:64px;color:var(--blue);line-height:1}
.stars{display:flex;justify-content:center;align-items:center;gap:2px;margin-top:8px}
.gdot{width:18px;height:18px;border-radius:50%;background:#4a86e8;margin-right:3px}
.tcard p{font-style:italic;font-size:14.5px;line-height:27px;margin-top:12px}
.avatar{width:74px;height:74px;border-radius:50%;background:radial-gradient(circle at 50% 40%,#c99878,#6b4a36)}
.who{width:446px;text-align:center;font-family:'Poppins',sans-serif;font-size:15.5px;line-height:28px}

/* contact */
.contact{left:0;top:2468px;width:1200px;height:590px;overflow:hidden}
.contact-bg{left:0;top:0;width:1200px;height:590px;
  background:linear-gradient(180deg,#2f69b0 0%,#2a5fa6 50%,#2c6ab5 100%)}
.contact h2{top:78px;color:#fff;font-family:'Poppins',sans-serif;font-size:40px;font-weight:400}
.contact h2 b{font-weight:600}
.field{height:42px;background:#fff;border-radius:22px;display:flex;align-items:center;gap:12px;
  padding-left:26px;font-size:15px;color:#555}
.field svg{width:18px;height:18px}
.msg{height:82px;align-items:flex-start;padding-top:16px;border-radius:40px}
.submit{left:520px;top:412px;width:161px;height:45px;background:#fff;border-radius:24px;color:var(--blue);
  font-weight:700;font-size:19px;display:flex;align-items:center;justify-content:center}

/* footer */
.foot-brand{top:3185px;width:1200px;text-align:center;font-size:50px}
.foot-mark{left:566px;top:3100px;width:68px;height:68px;border-radius:50%;background:var(--blue)}
.flinks{width:1200px;display:flex;justify-content:center;gap:22px;font-size:15px}
.social{top:3356px;left:534px;display:flex;gap:14px}
.social i{width:22px;height:22px;border-radius:50%;background:var(--blue);display:block}
.rule{left:0;top:3408px;width:1200px;height:1px;background:#ddd}
.copy{top:3436px;width:1200px;text-align:center;font-size:13.5px;font-weight:700}
</style>
</head>
<body>

<!-- HERO -->
<section class="abs hero">
  <div class="abs hero-scene" role="img" aria-label="Cruise ship on a turquoise sea beside a tropical island"></div>
  <svg class="abs hero-wave" width="1200" height="122" viewBox="0 0 1200 122">
    <path d="M0 70 Q600 150 1200 70 L1200 122 L0 122Z" fill="#fff"/>
    <path d="M0 50 Q600 140 1200 50 L1200 70 Q600 150 0 70Z" fill="#0f3f84"/>
  </svg>
  <nav class="abs nav">
    <a class="on">Home</a><a>About Us</a><a>Cruise Lines</a><a>Destinations</a>
    <a class="right">Itineraries</a><a>Blog/TravelTips</a>
    <span class="cta">Contact Us</span>
  </nav>
  <div class="abs logo-disc"><span class="brand">Glacera</span></div>
  <h1 class="abs">Adventure Awaits,<br><span>Set Sail Today!</span></h1>
  <div class="abs btn get">Get Started</div>
  <div class="abs search">
    <div class="chip"><svg viewBox="0 0 20 20"><path d="M10 1a6 6 0 0 0-6 6c0 5 6 12 6 12s6-7 6-12a6 6 0 0 0-6-6zm0 8a2 2 0 1 1 0-4 2 2 0 0 1 0 4z" fill="#2b6cb8"/></svg>Region</div>
    <div class="chip"><svg viewBox="0 0 20 20"><rect x="2" y="4" width="16" height="14" rx="2" fill="#2b6cb8"/><rect x="4" y="8" width="12" height="8" fill="#fff"/><rect x="5" y="9" width="3" height="2" fill="#2b6cb8"/><rect x="9" y="9" width="3" height="2" fill="#2b6cb8"/><rect x="5" y="12" width="3" height="2" fill="#2b6cb8"/></svg>Departure Date</div>
    <div class="chip"><svg viewBox="0 0 20 20"><path d="M10 1a6 6 0 0 0-6 6c0 5 6 12 6 12s6-7 6-12a6 6 0 0 0-6-6zm0 8a2 2 0 1 1 0-4 2 2 0 0 1 0 4z" fill="#2b6cb8"/></svg>Departure Post</div>
    <div class="chip"><svg viewBox="0 0 20 20"><circle cx="10" cy="10" r="7" fill="#2b6cb8"/><path d="M10 5v5h4" stroke="#fff" stroke-width="2" fill="none"/></svg>Duration</div>
    <div class="chip"><svg viewBox="0 0 20 20"><path d="M1 12h18l-3 5H4z" fill="#2b6cb8"/><rect x="5" y="6" width="9" height="5" fill="#2b6cb8"/></svg>Ships</div>
    <div class="btn sbtn"><svg width="22" height="22" viewBox="0 0 22 22"><circle cx="9" cy="9" r="7" stroke="#fff" stroke-width="3" fill="none"/><path d="M14 14l6 6" stroke="#fff" stroke-width="3"/></svg>Search</div>
  </div>
</section>

<!-- FEATURED OFFERS -->
<h2 class="abs sec-title head" style="top:640px">Featured <span class="accent">Offers</span></h2>
<div class="abs offer" style="left:96px;top:721px">
  <div class="pic" role="img" aria-label="Cruise ship under a cloudy sky" style="background:linear-gradient(160deg,#9fb8d2,#dfe7ef 55%,#4f6f8e)"></div>
  <h3>Best&nbsp; Antarctic Cruises</h3>
  <p>Embark on the ultimate adventure to the<br>Southern Hemisphere. Explore pristine<br><b>Price:</b> Starting at $3,499 per person</p>
</div>
<div class="abs offer sel" style="left:433px;top:721px">
  <div class="pic" role="img" aria-label="Traveler on a ship deck watching a sunset over the sea" style="background:linear-gradient(180deg,#e9c98a,#c58f4a 45%,#4a4a4c);border:2px solid #222"></div>
  <h3>Top Galápagos&nbsp; Cruises</h3>
  <p style="color:var(--ink)">Discover the breathtaking islands of the<br>Galápagos. Swim with sea lions, visit volcanic</p>
  <p style="margin-top:0"><b>Price:</b> Starting at $2,799 per person</p>
</div>
<div class="abs offer" style="left:769px;top:721px">
  <div class="pic" role="img" aria-label="Hands typing on a laptop showing last-minute deals" style="background:linear-gradient(140deg,#d8c7ae,#8b6e52 50%,#3d3a3a)"></div>
  <h3>Last-Minute Deals</h3>
  <p>Grab the best last-minute cruise deals before<br>they're gone! Limited dates and unbeatable<br><b>Price:</b> Starting at $1,299 per person</p>
</div>

<!-- DESTINATIONS -->
<section class="abs dest">
  <h2 class="abs sec-title head">Destinations</h2>
  <svg class="abs arrow" style="left:52px" width="16" height="22" viewBox="0 0 16 22"><path d="M12 2L4 11l8 9" stroke="#333" stroke-width="2.5" fill="none"/></svg>
  <svg class="abs arrow" style="left:1131px" width="16" height="22" viewBox="0 0 16 22"><path d="M4 2l8 9-8 9" stroke="#333" stroke-width="2.5" fill="none"/></svg>
  <div class="abs dcard" style="left:111px"><div class="pic" role="img" aria-label="Beach with palm trees in Mexico" style="background:linear-gradient(170deg,#8fc0e4,#4fb8c9 40%,#e8e2d2 70%,#5d6b3f)"></div><span>Mexico</span></div>
  <div class="abs dcard" style="left:359px"><div class="pic" role="img" aria-label="Colorful canal buildings in Italy" style="background:linear-gradient(170deg,#6fa6d8,#d49a6b 45%,#2e8fa3)"></div><span>Italy</span></div>
  <div class="abs dcard sel" style="left:607px"><div class="pic" role="img" aria-label="Harbour with opera house and bridge in Australia" style="background:linear-gradient(175deg,#8ec3ea,#5e9ec8 35%,#0e7a95)"></div><span>Australia</span></div>
  <div class="abs dcard" style="left:856px"><div class="pic" role="img" aria-label="City skyline across the water in New Zealand" style="background:linear-gradient(180deg,#7aa7d8,#bcc6cf 55%,#3e6d9e)"></div><span>New Zealand</span></div>
</section>

<!-- TESTIMONIALS -->
<h2 class="abs sec-title head" style="top:1988px">What Our Happy <span class="accent" style="font-weight:500">Travelers Are Saying</span></h2>
<div class="abs tcard" style="left:111px">
  <div class="quote">&ldquo;</div>
  <div class="stars"><i class="gdot"></i><span style="color:var(--star);font-size:20px">★★★★★</span></div>
  <p>"I can't even put into words how amazing our Antarctic cruise was! The scenery was breathtaking, and the crew made every moment special. I will definitely be booking</p>
</div>
<div class="abs tcard" style="left:640px">
  <div class="quote">&ldquo;</div>
  <div class="stars"><i class="gdot"></i><span style="color:var(--star);font-size:20px">★★★★★</span></div>
  <p>Our Mediterranean cruise was everything we hoped for and more. The food, the excursions, and the service were top-notch. It was truly a vacation of a lifetime!"</p>
</div>
<div class="abs avatar" style="left:297px;top:2238px" role="img" aria-label="Portrait of the reviewer"></div>
<div class="abs avatar" style="left:827px;top:2238px" role="img" aria-label="Portrait of the reviewer"></div>
<div class="abs who" style="left:111px;top:2318px">Hannah L.<br>New York, NY</div>
<div class="abs who" style="left:646px;top:2318px">Daniel K.<br>Los Angeles, CA</div>

<!-- CONTACT -->
<section class="abs contact">
  <div class="abs contact-bg" role="img" aria-label="Night city skyline reflected on water"></div>
  <h2 class="abs sec-title">Contact Us for Your <b>Next Cruise Adventure</b></h2>
  <div class="abs field" style="left:111px;top:172px;width:478px"><svg viewBox="0 0 18 18"><circle cx="9" cy="6" r="4" fill="#777"/><path d="M2 17a7 6 0 0 1 14 0z" fill="#777"/></svg>Name</div>
  <div class="abs field" style="left:610px;top:172px;width:476px"><svg viewBox="0 0 18 18"><path d="M4 1l3 4-2 2c1 3 3 5 6 6l2-2 4 3-2 3C8 17 1 10 1 3z" fill="#777"/></svg>Mobile Number</div>
  <div class="abs field" style="left:111px;top:232px;width:478px"><svg viewBox="0 0 18 18"><rect x="1" y="4" width="16" height="11" fill="#777"/><path d="M1 4l8 6 8-6" stroke="#fff" fill="none"/></svg>Email</div>
  <div class="abs field" style="left:610px;top:232px;width:478px"><svg viewBox="0 0 18 18"><path d="M9 2l8 4-8 4-8-4z" fill="#777"/><path d="M1 9l8 4 8-4M1 12l8 4 8-4" stroke="#777" fill="none"/></svg>Subject:</div>
  <div class="abs field msg" style="left:111px;top:301px;width:978px"><svg viewBox="0 0 18 18"><path d="M2 2h14v10H7l-4 4v-4H2z" fill="#777"/></svg>Message</div>
  <div class="abs submit">Submit</div>
  <svg class="abs" style="left:0;top:500px" width="1200" height="90" viewBox="0 0 1200 90"><path d="M0 90 Q600 -30 1200 80 L1200 90Z" fill="#000"/><path d="M0 90 Q600 -20 1200 90Z" fill="#fff"/></svg>
</section>

<!-- FOOTER -->
<div class="abs foot-mark"></div>
<div class="abs foot-brand brand">Glacera</div>
<div class="abs flinks" style="top:3260px"><span>Home</span><span>About Us</span><span>Cruise Lines</span><span>Destinations</span><span>Itineraries</span><span>Blog/TravelTips</span></div>
<div class="abs flinks" style="top:3306px;gap:56px"><span>Privacy Policy</span><span>Terms &amp; use</span><span>Cookie Policy</span></div>
<div class="abs social"><i></i><i></i><i></i><i></i></div>
<div class="abs rule"></div>
<div class="abs copy">Copyright © 2025 Glacera Voyages. All Rights Reserved.</div>

</body>
</html>
```